Automotive Accessories Business Card

Design a business template that match our new logo design and our industry.

https://www.qelmotorgear.com/

Target Market(s)

Aftermarket auto parts and accessories

Industry/Entity Type

automotive

Contact Information for Business Card

company logo

Font styles to use
Serif
Sans Serif

Colors
EB3D1F
EC4F4E
F09395
F8D3D4
FCEDEE

```html
<!DOCTYPE html>
<html lang="en">
<head>
<meta charset="utf-8">
<title>QEL Motor Gear – Business Card</title>
<link href="https://fonts.googleapis.com/css2?family=Montserrat:wght@400;700&display=swap" rel="stylesheet">
<style>
  :root {
    --backdrop: #9a9a9a;
    --card: #434142;
    --red: #d71f27;
    --band: #b9474b;
    --white: #ffffff;
    --text-light: #f2f2f2;
  }
  * { margin: 0; padding: 0; box-sizing: border-box; }
  html, body {
    width: 1200px; height: 1059px; overflow: hidden;
    background: var(--backdrop);
    font-family: 'Montserrat', sans-serif;
  }
  .canvas { position: relative; width: 1200px; height: 1059px; }
  .card {
    position: absolute;
    background: var(--card);
    overflow: hidden;
  }
  .card--front { left: 256px; top: 89px; width: 688px; height: 390px; }
  .card--back  { left: 253px; top: 569px; width: 694px; height: 394px; }

  .brand {
    position: absolute;
    display: flex; align-items: center; gap: 10px;
    color: var(--white);
    font-weight: 700;
    white-space: nowrap;
    line-height: 1;
  }
  .brand__square { background: var(--red); flex: none; }
  .card--front .brand {
    right: 31px; top: 83px; transform: translateY(-50%);
    font-size: 27px;
  }
  .card--front .brand__square { width: 24px; height: 24px; }
  .card--back .brand {
    left: 50%; top: 50%; transform: translate(-50%, -50%);
    font-size: 34px; gap: 12px;
  }
  .card--back .brand__square { width: 30px; height: 30px; }

  .person { position: absolute; left: 30px; top: 190px; }
  .person__name {
    color: var(--red); font-weight: 700; font-size: 25px;
    letter-spacing: 0.5px; line-height: 1;
  }
  .person__role {
    color: var(--text-light); font-weight: 400; font-size: 17px;
    margin-top: 7px; line-height: 1;
  }
  .divider {
    position: absolute; left: 30px; right: 31px; top: 258px;
    height: 1px; background: var(--red);
  }
  .contacts {
    position: absolute; left: 30px; top: 277px;
    list-style: none; color: var(--text-light);
    font-size: 16.5px; line-height: 27px;
  }
  .contacts li { display: flex; align-items: center; gap: 6px; }
  .contacts svg { width: 13px; height: 13px; flex: none; }
  .address {
    position: absolute; right: 31px; top: 311px;
    text-align: right; color: var(--text-light);
    font-size: 16.5px; line-height: 22px; font-style: normal;
  }
  .stripe {
    position: absolute; left: 0; right: 0; bottom: 0; height: 13px;
    background: var(--band);
  }
</style>
</head>
<body>
<div class="canvas">
  <section class="card card--front">
    <div class="brand"><span class="brand__square"></span>QEL MOTOR GEAR</div>

    <div class="person">
      <p class="person__name">DANA WHITFIELD</p>
      <p class="person__role">CEO/Founder</p>
    </div>
    <div class="divider"></div>

    <ul class="contacts">
      <li>
        <svg viewBox="0 0 24 24" aria-hidden="true"><path fill="#d71f27" d="M6.6 10.8c1.4 2.8 3.8 5.1 6.6 6.6l2.2-2.2c.3-.3.7-.4 1-.2 1.1.4 2.3.6 3.6.6.6 0 1 .4 1 1V20c0 .6-.4 1-1 1C10.6 21 3 13.4 3 4c0-.6.4-1 1-1h3.5c.6 0 1 .4 1 1 0 1.3.2 2.5.6 3.6.1.3 0 .7-.2 1z"/></svg>
        1-866-555-0142
      </li>
      <li>
        <svg viewBox="0 0 24 24" aria-hidden="true"><rect x="2" y="5" width="20" height="14" fill="#d71f27"/><path d="M2 6l10 7 10-7" fill="none" stroke="#434142" stroke-width="2"/></svg>
        sales@qelmotorgear.com
      </li>
      <li>
        <svg viewBox="0 0 24 24" aria-hidden="true"><g fill="none" stroke="#d71f27" stroke-width="2"><circle cx="12" cy="12" r="9"/><ellipse cx="12" cy="12" rx="4" ry="9"/><path d="M3 12h18M5 7h14M5 17h14"/></g></svg>
        www.qelmotorgear.com
      </li>
    </ul>

    <address class="address">240 W. Oak Ave. Suite B<br>Riverside, CA, 92501</address>

    <div class="stripe" role="img" aria-label="Checkered racing-flag band in white and red"></div>
  </section>

  <section class="card card--back">
    <div class="brand"><span class="brand__square"></span>QEL MOTOR GEAR</div>
  </section>
</div>
</body>
</html>
```